Tessaline Wellness Marketing Flyer

We are a new medical practice in the community and need a flyer to send to other medical offices to inform of our services. We just completed our logo with Draftmarketo and would like to incorporate that plus our marketing content into the flyer. Our medical practice has 2 divisions: (1)Mental Health/Psychiatry and (2) Migraine and Neurospasticity Management. Please see website for content and provider photos at www.TessaWellnet.com

Target Market(s)

Other Healthcare Professionals in the Community

Industry/Entity Type

Medical

Requirements
Must have
• Photos of all 5 healthcare providers, phone number, address, logo

```html
<!DOCTYPE html>
<html lang="en">
<head>
<meta charset="utf-8">
<title>Tessaline Wellness Flyer</title>
<link href="https://fonts.googleapis.com/css2?family=Libre+Baskerville:wght@400;700&family=Montserrat:wght@500;600;700&family=Open+Sans:wght@400;600;700;800&display=swap" rel="stylesheet">
<style>
:root{
  --stage:#ececec;
  --paper:#ffffff;
  --cream:#f2eddb;
  --forest:#153d22;
  --forest-panel:#164a2a;
  --teal:#12958a;
  --leaf:#8cb61f;
  --lime:#b9dc3c;
  --text:#2b2b2b;
  --photo-warm:#c98a4a;
  --photo-light:#f1d7a4;
}
*{box-sizing:border-box;margin:0;padding:0}
html,body{width:1200px;height:2302px;overflow:hidden;background:var(--stage)}
.flyer{position:absolute;left:50px;top:373px;width:1100px;height:1555px;background:var(--paper);overflow:hidden;box-shadow:0 10px 40px rgba(0,0,0,.18);font-family:"Open Sans",sans-serif;color:var(--text)}
.abs{position:absolute}
.backdrop{position:absolute;left:0;top:0}
.serif{font-family:"Libre Baskerville",serif}
.brand-mark{left:177px;top:57px;width:110px;height:110px;border-radius:50%;background:var(--teal)}
.brand-name{left:58px;top:184px;width:362px;text-align:center;font-family:"Libre Baskerville",serif;font-weight:400;color:var(--teal);line-height:1}
.brand-name .l1{display:block;font-size:46px;letter-spacing:1px}
.brand-name .l2{display:block;font-size:30px;letter-spacing:4px;margin-top:8px}
.headline{left:58px;top:289px;font-family:"Libre Baskerville",serif;font-weight:700;font-size:54px;line-height:62px;color:var(--forest)}
.tagline{left:59px;top:484px;font-family:"Montserrat",sans-serif;font-weight:500;font-size:18px;line-height:22px;color:#2d7a3a}
.section-title{font-family:"Libre Baskerville",serif;font-weight:700;color:var(--forest);font-size:24px;line-height:30px}
.body-copy{font-size:13.6px;line-height:17.8px;text-align:justify;color:#333}
.provider-photo{border-radius:14px;background:linear-gradient(160deg,#7a8a99,#3c4756);box-shadow:0 2px 6px rgba(0,0,0,.25)}
.provider-name{font-family:"Montserrat",sans-serif;font-weight:700;font-size:18px;color:var(--forest)}
.panel{left:578px;top:470px;width:463px;height:563px;background:var(--forest-panel);border-radius:0 0 22px 22px}
.panel .provider-name{color:var(--lime)}
.panel .body-copy{color:#e9f1e6;text-align:left}
.service{width:170px;text-align:center;font-family:"Libre Baskerville",serif;font-weight:700;font-size:13.5px;line-height:16px;color:var(--forest)}
.divider{width:0;border-left:2px dotted #555;height:95px;top:1265px}
.portal-item{left:899px;font-family:"Montserrat",sans-serif;font-weight:700;font-size:13.5px;color:#222}
.portal-dot{left:840px;width:42px;height:42px;border-radius:50%;background:var(--leaf)}
.cta{left:576px;top:1348px;font-family:"Libre Baskerville",serif;font-size:32px;letter-spacing:2px;color:var(--forest)}
.phone{left:635px;top:1396px;font-family:"Open Sans",sans-serif;font-weight:800;font-size:55px;color:#1e1e1e;letter-spacing:1px}
.footer-text{color:#fff;font-family:"Open Sans",sans-serif;font-weight:700}
</style>
</head>
<body>
<main class="flyer">

  <svg class="backdrop" width="1100" height="1555" viewBox="0 0 1100 1555" aria-hidden="true">
    <defs>
      <linearGradient id="creamFade" x1="0" y1="0" x2="0" y2="1">
        <stop offset="0" stop-color="#f3efdf"/>
        <stop offset="1" stop-color="#efe8d0"/>
      </linearGradient>
      <radialGradient id="photoTone" cx="0.5" cy="0.4" r="0.6">
        <stop offset="0" stop-color="#f6e2b5"/>
        <stop offset="0.55" stop-color="#d9a766"/>
        <stop offset="1" stop-color="#a9663a"/>
      </radialGradient>
    </defs>
    <path d="M0 0 H1100 V610 C1070 615 1050 620 1041 624 L578 590 C400 540 200 548 0 598 Z" fill="url(#creamFade)"/>
    <path d="M0 598 C200 548 400 543 580 590" fill="none" stroke="var(--forest)" stroke-width="5"/>
    <path d="M1041 626 C1060 616 1080 611 1100 608" fill="none" stroke="var(--forest)" stroke-width="5"/>
    <rect x="578" y="470" width="463" height="563" rx="22" fill="var(--forest-panel)"/>
    <rect x="578" y="470" width="463" height="40" fill="var(--forest-panel)"/>
    <circle cx="812" cy="307" r="313" fill="var(--teal)"/>
    <circle cx="800" cy="331" r="271" fill="url(#photoTone)" role="img" aria-label="Woman in a sunlit field making a heart shape with her hands, framed by green leaves"/>
    <path d="M0 1425 H427 C470 1425 490 1480 560 1480 H1100 V1555 H0 Z" fill="var(--leaf)"/>
  </svg>

  <div class="abs brand-mark"></div>
  <div class="abs brand-name"><span class="l1">TESSALINE</span><span class="l2">WELLNESS</span></div>

  <h1 class="abs headline">Helping Bodies<br>Helping Minds<br>Helping You</h1>
  <p class="abs tagline">Mental Health and Psychiatry Services<br>Migraine and Neurospasticity Intervention</p>

  <h2 class="abs section-title" style="left:57px;top:605px;font-size:25px">Meet Our Mental Health Providers</h2>
  <p class="abs body-copy" style="left:57px;top:644px;width:493px">Bringing comprehensive evaluation, medication management and psychotherapy to the full spectrum of mental health disorders including minor, moderate and major depression, bipolar disorder, ADD/ADHD, anxiety, schizophrenia, stress or grief reactions, and others.</p>

  <div class="abs provider-photo" style="left:60px;top:743px;width:112px;height:125px" role="img" aria-label="Portrait of Dean Marlow"></div>
  <h3 class="abs provider-name" style="left:187px;top:743px">DEAN MARLOW PMHNP - BC</h3>
  <p class="abs body-copy" style="left:189px;top:772px;width:361px">Formally from North Idaho and having moved back to this area, Dean brings several years of pediatric and adolescent experience to Tessaline Wellness. Outside of work, Dean enjoys spending time with his wife and two children, exploring various outdoor pursuits including backpacking, fishing, and all things Bigfoot.</p>

  <div class="abs provider-photo" style="left:60px;top:903px;width:112px;height:125px" role="img" aria-label="Portrait of Helen Brask"></div>
  <h3 class="abs provider-name" style="left:190px;top:903px">HELEN BRASK, PMHNP-BC</h3>
  <p class="abs body-copy" style="left:190px;top:931px;width:360px">Dr. Helen Brask is Board Certified in Geriatric and Adult Psychiatric Medicine. She has practiced Psychiatry for over 30 years and has extensive experience in the diagnosis and treatment of major mental illnesses. Her passion for mental wellness values the long term relationship with the adult and geriatric patient.</p>

  <h2 class="abs section-title" style="left:57px;top:1068px">Migraine and Neurospasticity<br>Intervention</h2>
  <p class="abs body-copy" style="left:57px;top:1147px;width:493px">Injections of botulinum neurotoxin are a widely used therapeutic form of treatment for both chronic migraines and patients with involuntary muscle contractions (neurospasticity). Injections may offer up to 3 months of relief and may be combined with other pharmacological interventions for maximum benefit.</p>

  <svg class="abs" style="left:80px;top:1258px" width="76" height="80" viewBox="0 0 76 80" aria-hidden="true">
    <circle cx="40" cy="40" r="34" fill="var(--lime)" opacity=".45"/>
    <path d="M10 32 C10 16 22 8 36 8 C50 8 62 16 62 32 C62 48 50 56 36 56 L22 66 L25 53 C15 49 10 41 10 32 Z" fill="#fff" stroke="var(--forest)" stroke-width="3"/>
    <circle cx="26" cy="32" r="3.5" fill="var(--forest)"/><circle cx="36" cy="32" r="3.5" fill="var(--forest)"/><circle cx="46" cy="32" r="3.5" fill="var(--forest)"/>
  </svg>
  <svg class="abs" style="left:260px;top:1258px" width="78" height="80" viewBox="0 0 78 80" aria-hidden="true">
    <circle cx="38" cy="40" r="34" fill="var(--lime)" opacity=".45"/>
    <rect x="14" y="8" width="40" height="56" rx="3" fill="#fff" stroke="var(--forest)" stroke-width="3"/>
    <path d="M22 22 H46 M22 31 H46 M22 40 H40 M22 49 H36" stroke="var(--forest)" stroke-width="3"/>
    <path d="M44 60 L66 34 L72 40 L50 66 L42 68 Z" fill="#fff" stroke="var(--forest)" stroke-width="3"/>
  </svg>
  <svg class="abs" style="left:450px;top:1258px" width="76" height="80" viewBox="0 0 76 80" aria-hidden="true">
    <circle cx="40" cy="42" r="34" fill="var(--lime)" opacity=".45"/>
    <rect x="10" y="14" width="54" height="50" rx="5" fill="#fff" stroke="var(--forest)" stroke-width="3"/>
    <path d="M10 26 H64 M22 8 V20 M52 8 V20" stroke="var(--forest)" stroke-width="3"/>
    <g fill="var(--forest)"><rect x="18" y="32" width="7" height="6"/><rect x="29" y="32" width="7" height="6"/><rect x="40" y="32" width="7" height="6"/><rect x="51" y="32" width="7" height="6"/><rect x="18" y="43" width="7" height="6"/><rect x="29" y="43" width="7" height="6"/><rect x="40" y="43" width="7" height="6"/><rect x="51" y="43" width="7" height="6"/><rect x="18" y="54" width="7" height="5"/><rect x="29" y="54" width="7" height="5"/></g>
  </svg>
  <div class="abs divider" style="left:202px"></div>
  <div class="abs divider" style="left:392px"></div>
  <p class="abs service" style="left:33px;top:1352px">New Patient<br>Evaluation</p>
  <p class="abs service" style="left:213px;top:1352px">Insurance<br>Pre-Authorization</p>
  <p class="abs service" style="left:402px;top:1352px">Follow-Up<br>Appointments</p>

  <div class="abs provider-photo" style="left:593px;top:704px;width:113px;height:126px" role="img" aria-label="Portrait of Paul Verrick"></div>
  <h3 class="abs provider-name" style="left:723px;top:702px;color:var(--lime)">PAUL VERRICK, PMHNP - BC</h3>
  <p class="abs body-copy" style="left:723px;top:730px;width:305px;color:#e9f1e6;text-align:left">Bringing comprehensive evaluation, medication management and psychotherapy to the full spectrum of mental health disorders including minor, moderate and major depression, bipolar disorder, ADD/ADHD, anxiety, schizophrenia, stress or grief reactions, and others.</p>

  <div class="abs provider-photo" style="left:593px;top:857px;width:113px;height:126px" role="img" aria-label="Portrait of Corinne Askew"></div>
  <h3 class="abs provider-name" style="left:723px;top:855px;color:var(--lime)">CORINNE ASKEW, PMHNP - BC</h3>
  <p class="abs body-copy" style="left:723px;top:890px;width:305px;color:#e9f1e6;text-align:left">With a former career in the inpatient behavioral health environment, Corinne is excited to share her experience and passion for mental health in an outpatient setting. Her practice cares for teenagers to adults in all aspects of psychiatry and mental wellness.</p>

  <h2 class="abs section-title" style="left:575px;top:1059px">Join us on the Portal!</h2>
  <p class="abs" style="left:576px;top:1093px;font-size:12px;color:#333">We know your days are busy!&nbsp; Use our Patient Portal for:</p>
  <div class="abs" style="left:576px;top:1131px;width:244px;height:187px;border-radius:12px;background:linear-gradient(135deg,#a8793f,#6d4a2c 55%,#c7a35f)" role="img" aria-label="Smiling family sitting together outdoors at an autumn pumpkin patch"></div>

  <div class="abs portal-dot" style="top:1128px"></div>
  <div class="abs portal-dot" style="top:1181px"></div>
  <div class="abs portal-dot" style="top:1235px"></div>
  <div class="abs portal-dot" style="top:1287px"></div>
  <svg class="abs" style="left:840px;top:1128px" width="42" height="202" viewBox="0 0 42 202" fill="none" stroke="#fff" stroke-width="2.2" aria-hidden="true">
    <path d="M11 20 C11 14 15 11 21 11 C27 11 31 14 31 20 C31 26 27 29 21 29 L15 32 L16 28 C13 26 11 23 11 20 Z"/>
    <path d="M14 83 L27 70 L31 74 L18 87 L13 88 Z"/>
    <rect x="10" y="128" width="15" height="12" rx="2"/><path d="M25 132 L32 128 V140 L25 136"/>
    <rect x="11" y="173" width="20" height="14" rx="1.5"/><path d="M15 178 H27 M15 182 H23"/>
  </svg>
  <p class="abs portal-item" style="top:1140px">Online Messaging</p>
  <p class="abs portal-item" style="top:1193px">Prescription Renewal</p>
  <p class="abs portal-item" style="top:1247px">Virtual Visits</p>
  <p class="abs portal-item" style="top:1299px">Pay Your Bill</p>

  <p class="abs cta">CALL US NOW!</p>
  <svg class="abs" style="left:579px;top:1412px" width="40" height="40" viewBox="0 0 40 40" aria-hidden="true">
    <circle cx="20" cy="20" r="17" fill="none" stroke="var(--leaf)" stroke-width="4"/>
    <path d="M13 12 L17 11 L19 16 L16.5 18 C17.5 21 19 22.5 22 23.5 L24 21 L29 23 L28 27 C20 28 12 20 13 12 Z" fill="var(--leaf)"/>
  </svg>
  <p class="abs phone">555-014-2290</p>

  <svg class="abs" style="left:64px;top:1442px" width="30" height="36" viewBox="0 0 30 36" aria-hidden="true">
    <path d="M15 2 C8 2 3 7 3 14 C3 23 15 34 15 34 C15 34 27 23 27 14 C27 7 22 2 15 2 Z" fill="#fff"/>
    <circle cx="15" cy="14" r="5" fill="var(--leaf)"/>
  </svg>
  <p class="abs footer-text" style="left:111px;top:1433px;font-size:22px;line-height:31px">218 W. Larchmont Ave, Suite B<br>Fernhill, ID 83000</p>
  <svg class="abs" style="left:62px;top:1513px" width="32" height="22" viewBox="0 0 32 22" aria-hidden="true">
    <rect x="1" y="1" width="30" height="20" rx="2" fill="#fff"/>
    <path d="M2 3 L16 13 L30 3" fill="none" stroke="var(--leaf)" stroke-width="2.5"/>
  </svg>
  <p class="abs footer-text" style="left:111px;top:1507px;font-size:22px">hello@TessaWellnet.com</p>
  <svg class="abs" style="left:583px;top:1500px" width="32" height="32" viewBox="0 0 32 32" fill="none" stroke="#fff" stroke-width="2.4" aria-hidden="true">
    <circle cx="16" cy="16" r="13"/><ellipse cx="16" cy="16" rx="6" ry="13"/><path d="M3 16 H29 M5 9 H27 M5 23 H27"/>
  </svg>
  <p class="abs footer-text" style="left:641px;top:1495px;font-size:29px">www.TessaWellnet.com</p>

</main>
</body>
</html>
```